whitening syringe artwork design

3ml syringe with silkscreen printing:
sample:
https://www.quorvashop.example/Velvo-Crane-Whitening-Syringes-Carbamide/dp/Q51842KX93/ref=sr_1_6?crid=7ZP42WQ81LMRT&dchild=1&keywords=whitening+syringes&qid=1698802214&sprefix=whitening+sy%2Caps%2C150&sr=8-6
inside the writing:
"teeth whitening gel " change to "Orvanne WHITENING GEL"
"Advanced formula" change to our logo and "Not all gels are created equal. "

additional requirements:
Inches: 2.01" wide x 1.34" around

CM: 5.1cm wide x 3.4cm around

See attached template: Generic_Syringe Labels 3ml_Silkscreen.pdf

- Leave the volume gage where it is, so it prints correctly on the syringe

- Feel free to change the color and font style

- An "identifying marker" is required: Teeth Whitening Syringe or Teeth Whitening Gel (for example)

- Replace "Teeth Whitening Gel - Advanced Formula" with your text and logo - it is there as a placeholder

-We require PDF files created to print ready specifications. Color images should be down-sampled to 300DPI

-Please provide us your Tintora color references for the color used in your artwork

https://www.tintora.example/color-finder#/pick?tintoraBook=tintoraSolidCoatedV3M2

-Please ensure that all fonts are embedded in the PDF document or make sure you convert fonts to outlines to prevent any issues with fonts (AI-Type-Create Outlines)

We will need your print ready artwork in a high resolution PDF file

teeth whitening ecommerce

• follow the guide document, and add text I want, color code from Tintora is provided

```html
<!DOCTYPE html>
<html lang="en">
<head>
<meta charset="utf-8">
<title>Whitening Syringe Silkscreen Artwork</title>
<link rel="stylesheet" href="https://fonts.googleapis.com/css2?family=Exo+2:wght@700&family=Barlow+Condensed:wght@700&family=Open+Sans:wght@600&display=swap">
<style>
  :root {
    --paper: #ffffff;
    --ink-navy: #27287a;
    --ink-blue: #2467b3;
  }
  html, body {
    margin: 0;
    padding: 0;
    width: 1200px;
    height: 718px;
    overflow: hidden;
    background: var(--paper);
  }
  .artboard {
    display: block;
    width: 1200px;
    height: 718px;
  }
  .product-title {
    font-family: "Exo 2", "Arial", sans-serif;
    font-weight: 700;
    fill: var(--ink-navy);
  }
  .brand-name {
    font-family: "Exo 2", "Arial", sans-serif;
    font-weight: 700;
    fill: var(--ink-navy);
  }
  .brand-dot { fill: var(--ink-navy); }
  .gauge-tick { fill: url(#gaugeInk); }
  .gauge-label {
    font-family: "Barlow Condensed", "Arial Narrow", sans-serif;
    font-weight: 700;
    fill: url(#gaugeInk);
  }
  .gauge-unit {
    font-family: "Open Sans", "Arial", sans-serif;
    font-weight: 600;
    fill: var(--ink-navy);
  }
</style>
</head>
<body>
<svg class="artboard" viewBox="0 0 1200 718" xmlns="http://www.w3.org/2000/svg">
  <defs>
    <linearGradient id="gaugeInk" x1="0" x2="0" y1="0" y2="1">
      <stop offset="0" stop-color="var(--ink-navy)"/>
      <stop offset="1" stop-color="var(--ink-blue)"/>
    </linearGradient>
  </defs>

  <g class="pen-label">
    <text class="product-title" x="308" y="234" font-size="44" text-anchor="middle" textLength="400" lengthAdjust="spacingAndGlyphs">Maren Whitening Pen</text>
    <text class="brand-name" x="311" y="268" font-size="24" text-anchor="middle" letter-spacing="5">HALVORY</text>
    <circle class="brand-dot" cx="311" cy="287" r="10"/>
  </g>

  <g class="pen-label">
    <text class="product-title" x="303" y="464" font-size="44" text-anchor="middle" textLength="400" lengthAdjust="spacingAndGlyphs">Maren Whitening Pen</text>
    <text class="brand-name" x="306" y="497" font-size="24" text-anchor="middle" letter-spacing="5">HALVORY</text>
    <circle class="brand-dot" cx="306" cy="516" r="10"/>
  </g>

  <g class="gel-label">
    <text class="product-title" x="880" y="281" font-size="36" text-anchor="middle" textLength="316" lengthAdjust="spacingAndGlyphs">Teeth Whitening Gel</text>
    <text class="brand-name" x="899" y="305" font-size="19" text-anchor="middle" letter-spacing="4">HALVORY</text>
    <circle class="brand-dot" cx="899" cy="319" r="8"/>
  </g>

  <g class="volume-gauge">
    <rect class="gauge-tick" x="657" y="394" width="3.5" height="63"/>
    <rect class="gauge-tick" x="727" y="420" width="3.5" height="37"/>
    <rect class="gauge-tick" x="796" y="394" width="3.5" height="63"/>
    <rect class="gauge-tick" x="876" y="420" width="3.5" height="37"/>
    <rect class="gauge-tick" x="955" y="394" width="3.5" height="63"/>
    <rect class="gauge-tick" x="1025" y="420" width="3.5" height="37"/>
    <rect class="gauge-tick" x="1094" y="394" width="3.5" height="63"/>

    <text class="gauge-label" transform="translate(736 397) rotate(-90)" font-size="26">½</text>
    <text class="gauge-label" transform="translate(805 384) rotate(-90)" font-size="26">1</text>
    <text class="gauge-label" transform="translate(886 409) rotate(-90)" font-size="26">1½</text>
    <text class="gauge-label" transform="translate(964 386) rotate(-90)" font-size="26">2</text>
    <text class="gauge-label" transform="translate(1033 411) rotate(-90)" font-size="26">2½</text>
    <text class="gauge-label" transform="translate(1104 386) rotate(-90)" font-size="26">3</text>
    <text class="gauge-unit" transform="translate(1119 451) rotate(-90)" font-size="17">ml/cc</text>
  </g>
</svg>
</body>
</html>
```